Ward Compass Business Card Design*

We need a business card design for our company Ward Compass. Our company is specialized in providing online consulting services regarding medical institutions, hospitals and doctors. We work with patients worldwide looking to choose between healthcare providers. We have a website you may use as a reference, where we list doctors and clinics worldwide. So we target Medical providers as well as patients worldwide.
Target Market(s)
Medical Providers and patients around the world
Industry/Entity Type
Medical
Contact Information for Business Card
Salwa Kettani
CEO
+90 612 348 2175
info@wardcompass.example
www.wardcompass.example
14 Annakhil 7 H.R.B. Rabat, Morocco
Requirements
Must have
- Company logo/name on one full side, personal info and smaller logo and company name on the other side.
Nice to have
- Smart and elegant design

```html
<!DOCTYPE html>
<html lang="en">
<head>
<meta charset="utf-8">
<title>Ward Compass Business Card</title>
<link rel="stylesheet" href="https://fonts.googleapis.com/css2?family=Lato:wght@400;700;900&display=swap">
<style>
  :root {
    --backdrop: #6e6e70;
    --card: #ffffff;
    --navy: #1d3461;
    --grey: #6f7377;
    --rule: #b9bcbf;
    --shadow: rgba(0, 0, 0, 0.35);
  }
  * { margin: 0; padding: 0; box-sizing: border-box; }
  html, body {
    width: 1200px;
    height: 1056px;
    overflow: hidden;
  }
  body {
    background: var(--backdrop);
    font-family: "Lato", Arial, sans-serif;
    position: relative;
  }
  .card {
    position: absolute;
    left: 270px;
    width: 660px;
    height: 377px;
    background: var(--card);
    box-shadow: 0 10px 24px var(--shadow);
  }
  .card--front { top: 110px; }
  .card--back { top: 569px; }

  .brand {
    position: absolute;
    display: flex;
    align-items: center;
    gap: 12px;
    color: var(--navy);
    font-weight: 700;
    letter-spacing: 0.06em;
    text-transform: uppercase;
    white-space: nowrap;
  }
  .brand__dot {
    border-radius: 50%;
    background: var(--navy);
    flex: none;
  }
  .card--front .brand { left: 48px; top: 52px; font-size: 22px; }
  .card--front .brand__dot { width: 34px; height: 34px; }
  .card--back .brand {
    left: 50%; top: 50%;
    transform: translate(-50%, -50%);
    font-size: 28px;
  }
  .card--back .brand__dot { width: 44px; height: 44px; }

  .holder {
    position: absolute;
    right: 40px;
    top: 150px;
    text-align: right;
  }
  .holder__name {
    color: var(--navy);
    font-weight: 900;
    font-size: 30px;
    letter-spacing: 0.01em;
    line-height: 1;
  }
  .holder__role {
    color: var(--grey);
    font-size: 14px;
    margin-top: 4px;
  }
  .divider {
    position: absolute;
    left: 40px;
    right: 40px;
    top: 213px;
    height: 1px;
    background: var(--rule);
  }
  .contact {
    position: absolute;
    list-style: none;
    color: var(--grey);
    font-size: 15px;
    line-height: 24px;
  }
  .contact li { display: flex; align-items: center; gap: 10px; }
  .contact svg { width: 12px; height: 12px; fill: #2b2b2b; flex: none; }
  .contact--online { right: 40px; top: 224px; }
  .contact--office { left: 40px; top: 300px; }
</style>
</head>
<body>
  <section class="card card--front">
    <div class="brand"><span class="brand__dot"></span>Ward Compass</div>
    <div class="holder">
      <div class="holder__name">SALWA KETTANI</div>
      <div class="holder__role">CEO</div>
    </div>
    <div class="divider"></div>
    <ul class="contact contact--online">
      <li>
        <svg viewBox="0 0 12 12"><path d="M0 2h12v8H0z M0 2l6 4 6-4" /><path d="M0.8 2.6 6 6.1l5.2-3.5" fill="none" stroke="#fff" stroke-width="1"/></svg>
        info@wardcompass.example
      </li>
      <li>
        <svg viewBox="0 0 12 12"><circle cx="6" cy="6" r="5.5"/><path d="M0.5 6h11M6 0.5c-2.5 3-2.5 8 0 11M6 0.5c2.5 3 2.5 8 0 11" fill="none" stroke="#fff" stroke-width="0.9"/></svg>
        www.wardcompass.example
      </li>
    </ul>
    <ul class="contact contact--office">
      <li>
        <svg viewBox="0 0 12 12"><path d="M2.3 0.6 4.4 3 3.3 4.4c.8 1.7 2.2 3.1 3.9 3.9L8.6 7.2 11 9.3 9.8 11.3C5 11 1 7 .7 2.2z"/></svg>
        +90 612 348 2175
      </li>
      <li>
        <svg viewBox="0 0 12 12"><path d="M6 0.3a4 4 0 0 1 4 4c0 3-4 7.4-4 7.4S2 7.3 2 4.3a4 4 0 0 1 4-4z"/><circle cx="6" cy="4.3" r="1.5" fill="#fff"/></svg>
        14 Annakhil 7 H.R.B. Rabat, Morocco
      </li>
    </ul>
  </section>

  <section class="card card--back">
    <div class="brand"><span class="brand__dot"></span>Ward Compass</div>
  </section>
</body>
</html>
```